Zilata - Sketches from a quiet road

🎨 Design Guidelines
1. Overall Impression

Dignified, spiritual, timeless

Central focus on sand dunes with footsteps as the main motif

Mood: calm, light, spirituality, hope

2. Color Scheme

Background: warm sand tones (beige, golden, brown)

Light source (sun/beam): soft gold/white

Typography: gold or warm yellow, metallic effect preferred (gold foil in print)

Spine and back cover: darker gradient from sand tones to deep blue/black for strong readability

3. Imagery

Front cover: sand dunes with clear footsteps leading towards light/horizon

No figurative depictions of people

Optional: subtle Islamic ornaments or geometric borders as a background accent

4. Typography

Title: “Zīlāta” → large, serif font, elegant, in gold

Subtitle: “Sketches From A Quiet Road” → smaller, clean & modern, also gold/white

Author: Idrīs-Wahīd Salmūn Qāzinī → bottom of the front cover, smaller size

Spine: Title + Arabic word زيلاتة vertically placed, harmonized with the style

5. Back Cover

Short blurb/description (provided by client)

Highlighted keywords in large type: "Courage. Integrity. Faith."

ISBN + barcode at the bottom left

Background: continuation of the sand texture from the front cover (with or without footsteps)

6. Finishing Options (Print)

Gold foil stamping for the title

Matte cover with selective gloss (eg on the light or ornaments)

High-quality, sturdy cover stock

Target Market(s)

Islamic

Font styles to use
Serif

Requirements
Must have
• read the guidelines!
Nice to have
• read the guidelines!
Should not have
• read the guidelines!

```html
<!DOCTYPE html>
<html lang="en">
<head>
<meta charset="utf-8">
<title>Zīlāta – Sketches From A Quiet Road – Cover Spread</title>
<link rel="stylesheet" href="https://fonts.googleapis.com/css2?family=Noto+Serif:wght@400&family=Noto+Naskh+Arabic:wght@400&family=Roboto:ital,wght@0,500;1,400&family=Montserrat:wght@400&display=swap">
<style>
  :root {
    --page-bg: #ffffff;
    --teal-deep: #056d8b;
    --teal: #0a7b95;
    --spine-teal: #07708d;
    --sky-light: #cfe6d0;
    --sun: #fbf6d8;
    --sand-light: #e9b25a;
    --sand: #d48f3e;
    --sand-dark: #a8652f;
    --sand-shadow: #5a3320;
    --dusk-grey: #5d5d5a;
    --text-white: #ffffff;
    --barcode-box: #ffffff;
  }
  html, body {
    margin: 0;
    padding: 0;
    width: 1200px;
    height: 1200px;
    overflow: hidden;
    background: var(--page-bg);
  }
  .spread {
    position: absolute;
    left: 67px;
    top: 220px;
    width: 1074px;
    height: 767px;
    color: var(--text-white);
  }
  .back-cover {
    position: absolute;
    left: 0; top: 0;
    width: 512px; height: 767px;
    background: linear-gradient(180deg,
      var(--teal-deep) 0%,
      var(--teal) 30%,
      #2d8193 45%,
      #4d7b83 58%,
      var(--dusk-grey) 72%,
      #6e5a4f 80%,
      #b48b58 90%,
      var(--sand) 100%);
  }
  .spine {
    position: absolute;
    left: 512px; top: 0;
    width: 50px; height: 767px;
    background: var(--spine-teal);
  }
  .front-cover {
    position: absolute;
    left: 562px; top: 0;
    width: 512px; height: 767px;
    overflow: hidden;
  }
  .front-scene {
    position: absolute;
    inset: 0;
    background:
      radial-gradient(ellipse 120px 60px at 52% 46%, rgba(255,252,235,0.95) 0%, rgba(252,240,190,0.6) 45%, rgba(252,240,190,0) 100%),
      linear-gradient(180deg,
        var(--teal-deep) 0%,
        var(--teal) 18%,
        #5ea8b8 30%,
        var(--sky-light) 38%,
        var(--sun) 45%,
        var(--sand-light) 50%,
        #e2a24c 62%,
        var(--sand) 75%,
        var(--sand-dark) 90%,
        var(--sand-shadow) 100%);
  }
  .title {
    position: absolute;
    margin: 0;
    font-family: "Noto Serif", serif;
    font-weight: 400;
    font-size: 108px;
    line-height: 1;
    letter-spacing: 4px;
    text-align: center;
    white-space: nowrap;
  }
  .subtitle {
    position: absolute;
    margin: 0;
    font-family: "Roboto", sans-serif;
    font-style: italic;
    font-weight: 400;
    font-size: 30px;
    letter-spacing: 1px;
    line-height: 1;
    text-align: center;
    white-space: nowrap;
  }
  .back-cover .title { left: 27px; width: 457px; top: 30px; }
  .back-cover .subtitle { left: 0; width: 512px; top: 157px; }
  .front-cover .title { left: 30px; width: 452px; top: 27px; }
  .front-cover .subtitle { left: 0; width: 512px; top: 154px; }
  .blurb {
    position: absolute;
    left: 27px;
    top: 193px;
    width: 457px;
    font-family: "Montserrat", sans-serif;
    font-size: 14px;
    line-height: 25px;
  }
  .blurb p {
    margin: 0 0 25px;
    text-align: justify;
    text-align-last: center;
  }
  .barcode-box {
    position: absolute;
    left: 314px;
    top: 639px;
    width: 170px;
    height: 92px;
    background: var(--barcode-box);
  }
  .spine-arabic {
    position: absolute;
    left: 25px;
    top: 90px;
    transform: translate(-50%, -50%) rotate(90deg);
    font-family: "Noto Naskh Arabic", serif;
    font-size: 40px;
    line-height: 1;
    white-space: nowrap;
  }
  .spine-author {
    position: absolute;
    left: 25px;
    top: 538px;
    transform: translate(-50%, -50%) rotate(90deg);
    font-family: "Roboto", sans-serif;
    font-weight: 500;
    font-size: 20px;
    letter-spacing: 1.6px;
    white-space: nowrap;
  }
  .front-author {
    position: absolute;
    left: 0;
    width: 512px;
    top: 703px;
    margin: 0;
    font-family: "Roboto", sans-serif;
    font-weight: 500;
    font-size: 25px;
    letter-spacing: 3px;
    text-align: center;
    white-space: nowrap;
  }
</style>
</head>
<body>
  <div class="spread">
    <section class="back-cover">
      <h2 class="title">ZĪLĀTA</h2>
      <p class="subtitle">Sketches From A Quiet Road</p>
      <div class="blurb">
        <p>Lorem Ipsum is simply dummy text of the printing and typesetting industry. Lorem Ipsum has been the industry's standard dummy text ever since the 1500s, when an unknown printer took a galley of type and scrambled it to make a type specimen book. It has survived not only five centuries, but also the leap into electronic typesetting,</p>
        <p>remaining essentially unchanged. It was popularised in the 1960s with the release of Typesheet sheets containing Lorem Ipsum passages, and more recently with desktop publishing software like Folio Layoutdesk including versions of Lorem Ipsum.</p>
      </div>
      <div class="barcode-box" aria-hidden="true"></div>
    </section>

    <section class="spine">
      <span class="spine-arabic" lang="ar" dir="rtl">زيلاتة</span>
      <span class="spine-author">Idrīs-Wahīd Salmūn Qāzinī</span>
    </section>

    <section class="front-cover">
      <div class="front-scene" role="img" aria-label="Photograph of golden sand dunes with a trail of footprints leading towards the rising sun on the horizon under a teal sky"></div>
      <h1 class="title">ZĪLĀTA</h1>
      <p class="subtitle">Sketches From A Quiet Road</p>
      <p class="front-author">Idrīs-Wahīd Salmūn Qāzinī</p>
    </section>
  </div>
</body>
</html>
```